Brisbane IT support business needs our first website

Hi All,

We are after a new website design for our IT solutions and support business.The business name is Harbourline Computing Services Group, or HCSG for short. We provide a range of solutions and services within the IT space.

I would like to utilize the two colours in our business logo I have uploaded.

I understand this is initially for the design only aspect of the site, but I would like to engage the winner to finish coding the website and finalize after also.

Target Market(s)

Other businesses owners and home users.

Industry/Entity Type

Business

Requirements
Must have
• Nice clean and functional design utilizing our business colours from the logo.

```html
<!DOCTYPE html>
<html lang="en">
<head>
<meta charset="utf-8">
<title>HCSG – IT Solutions and Support</title>
<link href="https://fonts.googleapis.com/css2?family=Lato:wght@300;400;700;900&display=swap" rel="stylesheet">
<style>
:root{
  --orange:#f5821f;
  --orange-dark:#e0701a;
  --navy:#0f4a66;
  --ink:#2d3238;
  --text:#6b7178;
  --light:#f2f3f5;
  --line:#e2e4e7;
  --hero:#22262c;
  --footer-top:#33383f;
  --footer-bottom:#25292e;
  --white:#ffffff;
}
*{box-sizing:border-box;margin:0;padding:0}
html,body{width:1200px;height:2692px;overflow:hidden}
body{font-family:'Lato',Arial,sans-serif;color:var(--text);background:var(--white);font-size:14px}
section,header,footer{position:relative;width:1200px;overflow:hidden}
.orange{color:var(--orange)}

/* header */
.site-header{height:112px;background:var(--white);border-bottom:1px solid var(--line)}
.brand{position:absolute;left:128px;top:20px;display:flex;align-items:center;gap:12px}
.brand-dot{width:64px;height:64px;border-radius:50%;background:var(--navy)}
.brand-name{font-size:34px;font-weight:900;color:var(--orange);letter-spacing:1px}
.top-contact{position:absolute;right:130px;top:18px;display:flex;gap:22px;font-size:13px;color:var(--ink)}
.top-contact span{display:flex;align-items:center;gap:6px}
.top-contact svg{width:14px;height:14px;fill:var(--navy)}
.main-nav{position:absolute;right:130px;top:56px;display:flex}
.main-nav a{display:block;padding:10px 11px;font-size:15px;color:var(--ink);text-decoration:none}
.main-nav a.active{background:var(--orange);color:var(--white)}

/* hero */
.hero{height:628px;background:linear-gradient(160deg,#3a3f46 0%,#23272d 45%,#17191d 100%);color:var(--white);text-align:center}
.hero-title{position:absolute;top:86px;left:0;right:0;font-size:50px;font-weight:300;line-height:1.15}
.hero-title strong{font-weight:900;color:var(--orange)}
.hero-features{position:absolute;top:270px;left:150px;right:150px;display:flex;justify-content:space-around}
.feature{width:240px}
.feature svg{width:80px;height:80px;stroke:var(--white);fill:none;stroke-width:2.5}
.feature p{margin-top:18px;font-size:21px}

/* about */
.about{height:204px;background:var(--light);text-align:center;padding-top:24px}
.section-title{font-size:32px;font-weight:400;color:var(--ink)}
.section-sub{font-size:15px;color:var(--ink);margin-top:4px}
.about p.body{width:940px;margin:14px auto 0;font-size:12px;line-height:1.55}

/* services */
.services{height:516px;text-align:center;padding-top:40px}
.services .section-sub,.partners .section-sub{color:var(--orange)}
.service-grid{position:absolute;top:150px;left:140px;width:920px;display:grid;grid-template-columns:1fr 1fr;row-gap:58px;column-gap:60px;text-align:left}
.service{display:flex;gap:20px}
.service-icon{flex:0 0 74px;height:74px;border-radius:50%;background:var(--navy);display:flex;align-items:center;justify-content:center}
.service-icon svg{width:36px;height:36px;fill:none;stroke:var(--white);stroke-width:2.5}
.service h3{font-size:19px;color:var(--orange);font-weight:700;margin-bottom:6px}
.service p{font-size:12px;line-height:1.6}

/* portfolio */
.portfolio{height:280px;background:var(--navy);color:var(--white);text-align:center;padding-top:26px}
.portfolio .section-title{color:var(--white)}
.portfolio .section-sub{color:#cfe0ea}
.portfolio-media{position:absolute;left:300px;top:112px;width:300px;height:144px;background:linear-gradient(135deg,#8ea7b8,#3f5e72)}
.portfolio-copy{position:absolute;left:620px;top:108px;width:300px;text-align:left}
.portfolio-copy h3{font-size:18px;font-weight:700;display:flex;align-items:center;gap:8px}
.portfolio-copy h3 i{width:18px;height:18px;border-radius:50%;background:var(--orange);display:block}
.portfolio-copy p{font-size:11px;line-height:1.55;margin:6px 0 10px;color:#d6e3ec}
.btn-outline{display:inline-block;border:1px solid var(--white);padding:5px 14px;font-size:13px;color:var(--white)}
.arrow{position:absolute;top:160px;width:18px;height:36px;stroke:#9fbccc;stroke-width:3;fill:none}
.arrow.left{left:140px}.arrow.right{right:140px}

/* partners */
.partners{height:340px;text-align:center;padding-top:28px}
.partner-grid{position:absolute;top:132px;left:200px;width:800px;display:grid;grid-template-columns:repeat(4,1fr)}
.partner{height:84px;display:flex;align-items:center;justify-content:center;border-right:1px solid var(--line);border-bottom:1px solid var(--line)}
.partner:nth-child(4n){border-right:none}
.partner:nth-child(n+5){border-bottom:none}
.partner span{width:130px;height:30px;border-radius:4px;background:#d4d7db}

/* call to action */
.cta{height:240px;background:var(--orange);color:var(--white);text-align:center;padding-top:34px}
.cta h2{font-size:31px;font-weight:400}
.cta .section-sub{color:var(--white)}
.cta p.body{width:900px;margin:16px auto 18px;font-size:12px;line-height:1.55;color:#fff3e6}
.btn-contact{display:inline-flex;align-items:center;gap:6px;border:1px solid var(--white);padding:7px 16px;font-size:14px}

/* contact */
.contact{height:300px;background:var(--footer-top);color:#d5d9dd}
.contact h2{position:absolute;left:132px;top:28px;font-size:26px;font-weight:400;color:var(--white)}
.contact-list{position:absolute;left:140px;top:82px;list-style:none;font-size:13px;line-height:1.5}
.contact-list li{display:flex;gap:12px;margin-bottom:16px}
.contact-list svg{flex:0 0 16px;height:16px;fill:var(--white);margin-top:2px}
.map{position:absolute;left:620px;top:52px;width:410px;height:200px;background:linear-gradient(135deg,#e9e6de,#d7dccf)}
.map-link{position:absolute;left:620px;top:262px;font-size:13px;color:var(--white)}

/* footer */
.site-footer{height:72px;background:var(--footer-bottom);display:flex;align-items:center;justify-content:space-between;padding:0 140px}
.social{display:flex;gap:10px}
.social span{width:26px;height:26px;border-radius:50%;background:var(--orange)}
.copyright{font-size:12px;color:#9aa0a6}
</style>
</head>
<body>

<header class="site-header">
  <div class="brand"><span class="brand-dot"></span><span class="brand-name">HCSG</span></div>
  <div class="top-contact">
    <span><svg viewBox="0 0 24 24"><path d="M6.6 10.8a15 15 0 0 0 6.6 6.6l2.2-2.2a1 1 0 0 1 1-.25 11.4 11.4 0 0 0 3.6.57 1 1 0 0 1 1 1V20a1 1 0 0 1-1 1A17 17 0 0 1 3 4a1 1 0 0 1 1-1h3.5a1 1 0 0 1 1 1c0 1.25.2 2.45.57 3.57a1 1 0 0 1-.25 1z"/></svg>Call us: (07) 5550 1842</span>
    <span><svg viewBox="0 0 24 24"><path d="M2 5h20v14H2z M2 5l10 8 10-8" /></svg>Email: hello@hcsg-services.example</span>
  </div>
  <nav class="main-nav">
    <a class="active">Home</a><a>About Us</a><a>Services</a><a>Technology</a><a>Solutions</a><a>Support</a><a>Contact</a>
  </nav>
</header>

<section class="hero" role="img" aria-label="Dark photo of a laptop on a desk behind the headline">
  <h1 class="hero-title"><strong>Success</strong> With<br>Our Creative Solutions</h1>
  <div class="hero-features">
    <div class="feature">
      <svg viewBox="0 0 80 80"><rect x="8" y="12" width="64" height="42" rx="2"/><path d="M30 66h20M40 54v12M28 28l-8 6 8 6M52 28l8 6-8 6M44 24l-8 20"/></svg>
      <p>Web Development</p>
    </div>
    <div class="feature">
      <svg viewBox="0 0 80 80"><rect x="8" y="12" width="64" height="50" rx="2"/><path d="M8 22h64M18 52l12-12 10 8 16-16"/></svg>
      <p>Online Marketing</p>
    </div>
    <div class="feature">
      <svg viewBox="0 0 80 80"><rect x="8" y="12" width="64" height="42" rx="2"/><path d="M30 66h20M40 54v12"/><circle cx="40" cy="33" r="8"/><path d="M40 19v5M40 42v5M26 33h5M49 33h5"/></svg>
      <p>Software Development</p>
    </div>
  </div>
</section>

<section class="about">
  <h2 class="section-title">About <span class="orange">HCSG</span></h2>
  <p class="section-sub">Lorem ipsum dolor sit amet, consectetuer adipiscing elit, sed diam nonummy.</p>
  <p class="body">Sed diam nonummy nibh euismod tincidunt ut laoreet dolore magna aliquam erat volutpat. Ut wisi enim ad minim veniam, quis nostrud exerci tation ullamcorper suscipit lobortis nisl ut aliquip ex ea commodo consequat. Duis autem vel eum iriure dolor in hendrerit in vulputate velit esse molestie consequat, vel illum dolore eu feugiat nulla facilisis at vero eros et accumsan et iusto odio dignissim qui blandit praesent luptatum zzril delenit augue duis dolore te feugait nulla facilisi. Lorem ipsum dolor sit amet, consectetuer adipiscing elit.</p>
</section>

<section class="services">
  <h2 class="section-title">Our <span class="orange">Services</span></h2>
  <p class="section-sub">Providing the best quality services</p>
  <div class="service-grid">
    <div class="service">
      <div class="service-icon"><svg viewBox="0 0 36 36"><path d="M8 28l12-12M22 6a7 7 0 0 0 8 8l-4-4z"/></svg></div>
      <div><h3>IT Support</h3><p>Lorem ipsum dolor sit amet, consectetuer adipiscing elit, sed diam nonummy nibh euismod tincidunt ut laoreet dolore magna aliquam erat volutpat.</p></div>
    </div>
    <div class="service">
      <div class="service-icon"><svg viewBox="0 0 36 36"><ellipse cx="18" cy="9" rx="10" ry="4"/><path d="M8 9v18c0 2 4.5 4 10 4s10-2 10-4V9M8 18c0 2 4.5 4 10 4s10-2 10-4"/></svg></div>
      <div><h3>Data Management</h3><p>Lorem ipsum dolor sit amet, consectetuer adipiscing elit, sed diam nonummy nibh euismod tincidunt ut laoreet dolore magna aliquam erat volutpat.</p></div>
    </div>
    <div class="service">
      <div class="service-icon"><svg viewBox="0 0 36 36"><path d="M6 6v24h24M10 24l7-8 5 4 8-10"/></svg></div>
      <div><h3>Fast Results</h3><p>Lorem ipsum dolor sit amet, consectetuer adipiscing elit, sed diam nonummy nibh euismod tincidunt ut laoreet dolore magna aliquam erat volutpat.</p></div>
    </div>
    <div class="service">
      <div class="service-icon"><svg viewBox="0 0 36 36"><rect x="9" y="16" width="18" height="14" rx="2"/><path d="M12 16v-4a6 6 0 0 1 12 0v4"/></svg></div>
      <div><h3>100% Secure</h3><p>Lorem ipsum dolor sit amet, consectetuer adipiscing elit, sed diam nonummy nibh euismod tincidunt ut laoreet dolore magna aliquam erat volutpat.</p></div>
    </div>
  </div>
</section>

<section class="portfolio">
  <h2 class="section-title">Our Work Portfolio</h2>
  <p class="section-sub">We deliver top quality products</p>
  <svg class="arrow left" viewBox="0 0 18 36"><path d="M15 3L3 18l12 15"/></svg>
  <div class="portfolio-media" role="img" aria-label="Project image showing a hand touching a cloud computing graphic"></div>
  <div class="portfolio-copy">
    <h3><i></i>Project Name</h3>
    <p>Sed diam nonummy nibh euismod tincidunt ut laoreet dolore magna aliquam erat volutpat. Ut wisi enim ad minim veniam, quis nostrud exerci tation ullamcorper suscipit lobortis nisl ut aliquip ex ea commodo consequat. Duis autem vel eum iriure dolor in hendrerit in vulputate velit.</p>
    <span class="btn-outline">View Project</span>
  </div>
  <svg class="arrow right" viewBox="0 0 18 36"><path d="M3 3l12 15L3 33"/></svg>
</section>

<section class="partners">
  <h2 class="section-title">Our <span class="orange">Partners</span></h2>
  <p class="section-sub">Lorem ipsum dolor sit amet consectetuer</p>
  <div class="partner-grid">
    <div class="partner"><span></span></div><div class="partner"><span></span></div><div class="partner"><span></span></div><div class="partner"><span></span></div>
    <div class="partner"><span></span></div><div class="partner"><span></span></div><div class="partner"><span></span></div><div class="partner"><span></span></div>
  </div>
</section>

<section class="cta">
  <h2>We Can Help Build Your Project</h2>
  <p class="section-sub">Tell Us About Your Project</p>
  <p class="body">Sed diam nonummy nibh euismod tincidunt ut laoreet dolore magna aliquam erat volutpat. Ut wisi enim ad minim veniam, quis nostrud exerci tation ullamcorper suscipit lobortis nisl ut aliquip ex ea commodo consequat. Duis autem vel eum iriure dolor in hendrerit in vulputate.</p>
  <span class="btn-contact">Contact us <svg width="12" height="12" viewBox="0 0 12 12" fill="none" stroke="#fff" stroke-width="2"><path d="M4 2l4 4-4 4"/></svg></span>
</section>

<section class="contact">
  <h2>Contact Info</h2>
  <ul class="contact-list">
    <li><svg viewBox="0 0 24 24"><path d="M12 2a7 7 0 0 0-7 7c0 5 7 13 7 13s7-8 7-13a7 7 0 0 0-7-7zm0 9.5a2.5 2.5 0 1 1 0-5 2.5 2.5 0 0 1 0 5z"/></svg><span>Harbourline Computing Services Group<br>18 Quayside Lane, Riverton<br>QLD 4000, Australia</span></li>
    <li><svg viewBox="0 0 24 24"><path d="M6.6 10.8a15 15 0 0 0 6.6 6.6l2.2-2.2a1 1 0 0 1 1-.25 11.4 11.4 0 0 0 3.6.57 1 1 0 0 1 1 1V20a1 1 0 0 1-1 1A17 17 0 0 1 3 4a1 1 0 0 1 1-1h3.5a1 1 0 0 1 1 1c0 1.25.2 2.45.57 3.57a1 1 0 0 1-.25 1z"/></svg><span>(07) 5550 1842</span></li>
    <li><svg viewBox="0 0 24 24"><path d="M2 5h20v14H2zm2 2v.5l8 6 8-6V7z"/></svg><span>hello@hcsg-services.example</span></li>
  </ul>
  <div class="map" role="img" aria-label="Street map showing the office location"></div>
  <span class="map-link">View Full Map &rsaquo;</span>
</section>

<footer class="site-footer">
  <div class="social"><span></span><span></span><span></span><span></span><span></span></div>
  <p class="copyright">© 2016 Harbourline Computing Services Group. All Rights Reserved.</p>
</footer>

</body>
</html>
```